Construction material supplies company business card ****

1. Full company name “K T Masonry Works Ltd”
I am after a Business card design for the company as a whole. We are better known in Solomon Islands as “K T Masonry” for short.

We are a building materials supplier of
Ready Mixed Concrete, Bricks and Blocks,
Quarry products- gravel, aggregates, sand etc.
Cement distributor/retailer of reputable brands.
Other prefab concrete products. Culverts, wave breakers, concrete retaining blocks etc.

2. Competitive Advantage over Competition: Quality, efficient, professional, dependable, reliable

3. We want people to feel trust worthy, high quality, strong when they see our brand

5. No preference to color. Maybe more sturdy and corporate. Not fancy.

Industry/Entity Type

CONSTRUCTION SUPPLY

Contact Information for Business Card

Name, Position, office phone mob phone, email

Requirements
Must have
• the company logo
Nice to have
• would like to see a mixture of designs, of with logo only and also with simple graphic designs to bring out the company whilst still have the strong sturdy professional feeling

```html
<!DOCTYPE html>
<html lang="en">
<head>
<meta charset="UTF-8">
<title>K T Masonry – Business Card</title>
<link rel="stylesheet" href="https://fonts.googleapis.com/css2?family=Archivo:wght@800&family=Roboto:wght@400&display=swap">
<style>
  :root {
    --navy: #15446a;
    --white: #ffffff;
    --disc: #f1eeee;
    --disc-edge: #dcd6d6;
    --stage: #e9e7e5;
  }
  * { box-sizing: border-box; margin: 0; padding: 0; }
  html, body {
    width: 1200px;
    height: 900px;
    overflow: hidden;
    background: var(--stage);
  }
  .card {
    position: absolute;
    left: 100px;
    top: 141px;
    width: 1000px;
    height: 617px;
    background: var(--navy);
    color: var(--white);
    font-family: "Roboto", Arial, sans-serif;
  }
  .holder {
    position: absolute;
    left: 33px;
    top: 170px;
  }
  .holder-name {
    font-family: "Archivo", "Arial Black", sans-serif;
    font-weight: 800;
    font-size: 40px;
    line-height: 44px;
    letter-spacing: 0.5px;
  }
  .holder-role {
    font-size: 27px;
    line-height: 32px;
    letter-spacing: 0.3px;
  }
  .contacts {
    position: absolute;
    left: 33px;
    top: 296px;
    list-style: none;
  }
  .contacts li {
    display: flex;
    align-items: center;
    height: 36.5px;
    font-size: 27px;
    letter-spacing: 0.3px;
  }
  .contacts svg {
    width: 28px;
    height: 28px;
    margin-right: 9px;
    flex: none;
  }
  .brand-disc {
    position: absolute;
    left: 459px;
    top: 59px;
    width: 498px;
    height: 498px;
    border-radius: 50%;
    background: radial-gradient(circle at 50% 45%, var(--white) 0%, var(--disc) 60%, var(--disc-edge) 100%);
    display: flex;
    align-items: center;
    justify-content: center;
  }
  .brand-name {
    font-family: "Archivo", "Arial Black", sans-serif;
    font-weight: 800;
    font-size: 52px;
    letter-spacing: 2px;
    color: var(--navy);
    white-space: nowrap;
  }
</style>
</head>
<body>
  <main class="card">
    <div class="holder">
      <h1 class="holder-name">DANIEL HARPER</h1>
      <p class="holder-role">Managing Director</p>
    </div>

    <ul class="contacts">
      <li>
        <svg viewBox="0 0 24 24" fill="none" stroke="currentColor" stroke-width="2" stroke-linecap="round" stroke-linejoin="round" aria-hidden="true">
          <path d="M5 3h4l2 5-2.5 1.5a11 11 0 0 0 6 6L16 13l5 2v4a2 2 0 0 1-2 2A16 16 0 0 1 3 5a2 2 0 0 1 2-2z"/>
          <path d="M14 3a7 7 0 0 1 7 7"/><path d="M14 7a3 3 0 0 1 3 3"/>
        </svg>
        055-210 348 672
      </li>
      <li>
        <svg viewBox="0 0 24 24" fill="none" stroke="currentColor" stroke-width="2" stroke-linecap="round" aria-hidden="true">
          <rect x="6" y="2" width="12" height="20" rx="2"/><line x1="11" y1="18" x2="13" y2="18"/>
        </svg>
        055-210 348 672
      </li>
      <li>
        <svg viewBox="0 0 24 24" fill="currentColor" aria-hidden="true">
          <path d="M2 6h20v12H2z M3.5 7l8.5 6.5L20.5 7z" fill-rule="evenodd"/>
        </svg>
        info@ktmasonry.com
      </li>
      <li>
        <svg viewBox="0 0 24 24" fill="none" stroke="currentColor" stroke-width="1.8" aria-hidden="true">
          <circle cx="12" cy="12" r="10"/><ellipse cx="12" cy="12" rx="4.5" ry="10"/>
          <line x1="2" y1="12" x2="22" y2="12"/><path d="M4 7h16M4 17h16"/>
        </svg>
        www.ktmasonry.com
      </li>
    </ul>

    <div class="brand-disc">
      <span class="brand-name">K T MASONRY</span>
    </div>
  </main>
</body>
</html>
```